Website Redesign - We Need Your Magic!

Hello we are looking for you to help us re-design a high end and professional website for a high-end private school.

Here is the current site: http://www.ferndalecrest.com/

NOTE THIS IS DESIGN ONLY, NO CODING :)

The image they want to portray is that of high quality sports and education, in a creative "un-stiff" way.

Menu Bar: Horizontal

Look and Feel:

Site Colors: Dark green and a Gold yellow (logos are attached)

This site will represent a school so the look must be clean, bold, and classy. The site must have a very clean user interface, with things easily recognizable. Think simple.

The site should be visually appealing! If you come to me with templates, or a ton of text you will be out.

This site should be outside the box, we do not want boring, we do not want status quo. This site should instill excitement, innovation, and athletics.

So the main points again are:

1. High-end and classy look, with creative feel
2. Simple and clear navigation style
3. To cover the Junior and High School - Ferndale Crest College Schools

Think outside the box. We look forward to seeing what you come up with!!

Thank you for helping us create an amazing site for the school!

Industry/Entity Type

School

```html
<!DOCTYPE html>
<html lang="en">
<head>
<meta charset="utf-8">
<title>Ferndale Crest College</title>
<link href="https://fonts.googleapis.com/css2?family=Raleway:wght@700&family=Arimo:wght@400;700&display=swap" rel="stylesheet">
<style>
:root{
  --green:#0e5a2a;
  --green-dark:#0a3f1d;
  --gold:#b69b10;
  --gold-text:#a9840f;
  --nav-active:#e5c416;
  --text:#222;
  --muted:#666;
  --footer:#2b2b2b;
  --footer-bar:#1e1e1e;
  --rule:#d8d8d8;
}
*{margin:0;padding:0;box-sizing:border-box}
html,body{width:900px;height:1200px;overflow:hidden}
body{position:relative;font-family:"Arimo",Arial,sans-serif;color:var(--text);background:#fff;font-size:10px}
.abs{position:absolute}
.header{left:0;top:0;width:900px;height:114px;background:radial-gradient(circle at 30% 20%,#fafafa,#eeeeee)}
.crest-mark{left:78px;top:18px;width:70px;height:70px;border-radius:50%;background:var(--green)}
.site-title{left:170px;top:36px;font-family:"Raleway",sans-serif;font-weight:700;font-size:25px;color:var(--green)}
.tagline{left:170px;top:74px;font-size:11px;color:#222;letter-spacing:.1px}
.contact{top:34px;font-size:11px;color:#333;display:flex;align-items:center;gap:6px}
.search{left:522px;top:65px;width:237px;height:27px;border:1px solid #ccc;background:#fff;font-size:10px;color:#777;padding:8px 8px}
.search-btn{left:763px;top:65px;width:62px;height:27px;background:var(--green);color:#fff;font-size:9px;font-weight:700;display:flex;align-items:center;justify-content:center;gap:3px}
.nav{left:0;top:114px;width:900px;height:34px;background:linear-gradient(#1a7a37,var(--green-dark))}
.nav ul{list-style:none;display:flex;position:absolute;left:76px;top:0;height:34px}
.nav li{color:#fff;font-weight:700;font-size:10.5px;line-height:34px;padding:0 15px;margin-right:10px}
.nav li.active{background:var(--nav-active);color:#222}
.hero{left:75px;top:163px;width:750px;height:261px;background:#fff;border:1px solid #ddd;box-shadow:0 1px 3px rgba(0,0,0,.15);padding:4px}
.hero-photo{width:100%;height:100%;background:linear-gradient(90deg,#6e5640,#b9b4a4 45%,#d9d3c8 70%,#8d8aa5)}
h2.section{font-family:"Arimo",sans-serif;font-weight:400;font-size:20px;color:var(--gold-text)}
.copy p{font-size:10px;line-height:15px;margin-bottom:15px}
.divider{left:75px;top:659px;width:486px;height:1px;background:var(--rule)}
.head-photo{left:77px;top:721px;width:136px;height:159px;background:linear-gradient(#2d6a55,#5a7d6a 55%,#c9a77e)}
.newsletter{left:599px;top:448px;width:226px;height:131px;background:var(--gold);padding:14px 16px;color:#fff}
.newsletter h3{font-size:18px;color:#111;font-weight:700;margin-bottom:8px}
.newsletter p{font-size:9.5px;line-height:14px}
.nl-field{position:absolute;left:16px;top:86px;width:160px;height:25px;background:#fff;color:#444;font-size:10px;padding:7px 7px}
.nl-go{position:absolute;left:176px;top:86px;width:37px;height:25px;background:var(--green);color:#fff;font-size:11px;text-align:center;line-height:25px;border-radius:0 4px 4px 0}
h3.side{font-weight:400;font-size:18.5px;color:var(--green)}
.side-rule{height:1px;background:var(--rule)}
.arrows{display:flex;gap:3px}
.arrows span{width:13px;height:13px;border-radius:2px;background:linear-gradient(#f2f2f2,#c8c8c8);font-size:8px;line-height:13px;text-align:center;color:#6a8a1a}
.cal{font-size:9.5px;line-height:15px;color:#222}
.event{font-size:9.5px;line-height:13.5px}
.event .date{display:block;text-align:right;color:var(--gold);font-style:italic;font-weight:700;font-size:9px}
.sports{list-style:none;font-size:10.5px;color:#333;letter-spacing:.3px}
.sports li{height:21px;display:flex;align-items:center;gap:9px}
.footer{left:0;top:1072px;width:900px;height:102px;background:var(--footer);color:#fff}
.footer h4{font-size:12px;font-weight:700;color:#f2f2f2}
.footer .small{font-size:8px;line-height:12px;color:#eee}
.footer .links{font-size:10px;line-height:16px;color:#eee}
.social{left:531px;top:44px;width:109px;height:33px;border:1px solid #ccc;background:#f4f4f4;display:flex;align-items:center;gap:6px;padding:0 6px;color:var(--green);font-weight:700;font-size:12px}
.social i{width:16px;height:16px;background:var(--green);display:block}
.copyright{left:0;top:1174px;width:900px;height:26px;background:var(--footer-bar);color:#ccc;font-size:10px;text-align:center;line-height:26px}
</style>
</head>
<body>
<header class="header abs">
  <div class="crest-mark abs"></div>
  <div class="site-title abs">Ferndale Crest College</div>
  <div class="tagline abs">Stepping Ahead in . Eduction . Culture &nbsp;. &nbsp;Sport . &nbsp;Life</div>
  <div class="contact abs" style="left:525px">
    <svg width="12" height="12" viewBox="0 0 24 24"><path fill="#222" d="M6.6 10.8a15 15 0 0 0 6.6 6.6l2.2-2.2c.3-.3.7-.4 1-.2 1.1.4 2.3.6 3.6.6.6 0 1 .4 1 1V20c0 .6-.4 1-1 1A17 17 0 0 1 3 4c0-.6.4-1 1-1h3.5c.6 0 1 .4 1 1 0 1.3.2 2.5.6 3.6.1.3 0 .7-.2 1z"/></svg>
    <span>0774 318 206 / 0774 552 917</span>
  </div>
  <div class="contact abs" style="left:686px">
    <svg width="14" height="10" viewBox="0 0 14 10"><rect width="14" height="10" fill="#e2b21c"/><path d="M0 0l7 5 7-5" stroke="#fff" fill="none"/></svg>
    <span>office@ferndalecrest.com</span>
  </div>
  <div class="search abs">Search you any keyword</div>
  <div class="search-btn abs">
    <svg width="8" height="8" viewBox="0 0 10 10"><circle cx="4" cy="4" r="3" stroke="#fff" fill="none" stroke-width="1.5"/><path d="M6.3 6.3L9 9" stroke="#fff" stroke-width="1.5"/></svg>Search
  </div>
</header>

<nav class="nav abs">
  <ul>
    <li class="active">HOME</li><li>ABOUT US</li><li>ACADEMICS</li><li>SPORTS</li><li>JOINING FERNDALE</li><li>WORKING AT THE COLLEGE</li><li>CONTACT US</li>
  </ul>
</nav>

<div class="hero abs"><div class="hero-photo" role="img" aria-label="Teacher helping pupils with written work in a classroom"></div></div>

<main>
  <h2 class="section abs" style="left:76px;top:449px">Welcome to Ferndale Crest College</h2>
  <div class="copy abs" style="left:77px;top:484px;width:480px">
    <p>Welcome to Ferndale Crest Group of Schools where our School Motto is ‘Simbiso’ meaning Togetherness. We aim to work together in every aspect of School life, from academics to sport.</p>
    <p>Ferndale Crest College opened on 14th February 1983 and occupies 120 ha of land amidst the low hills of the Mavuri Range, 8km west of Kelvindale. This location encourages focus on School life away from the distractions and hustle and bustle of the larger towns.</p>
    <p>The day scholars have the option of selected bus drop off points for parents to collect day scholars closer to home. Ferndale Crest College offers a wide range of academic subjects alongside a varied sport and extra-curricular program.</p>
  </div>
  <div class="divider abs"></div>

  <h2 class="section abs" style="left:76px;top:681px">Headmaster's Welcome Note</h2>
  <div class="head-photo abs" role="img" aria-label="Portrait photograph of the headmaster"></div>
  <div class="copy abs" style="left:224px;top:719px;width:340px">
    <p><b>Welcome to Ferndale Crest College.</b>&nbsp; Here at the College we aim to encourage each pupil to be a self-confident, well-rounded individual. We aim to propel them to the highest level of achievement in both academics and extra-curricular activities to provide them with the life skills they will need when they leave the College and to prepare them to be of value to society.</p>
    <p>The College is a warm community which lives out high standards and is rightly proud of its achievements.&nbsp; We are a small enough School for each pupil to be known well, but large enough to offer a wide range of subjects and experience.</p>
  </div>
  <div class="copy abs" style="left:79px;top:899px;width:480px">
    <p>Our Website covers many aspects of the College from how to apply for a place, to the curriculum and to much more.&nbsp; I hope you find it helpful and interesting.&nbsp; Please visit and meet the pupils, the staff and see for yourself what Ferndale Crest College can offer your son or daughter.&nbsp; I look forward to welcoming you and your family to Ferndale Crest College.</p>
  </div>
</main>

<aside>
  <div class="newsletter abs">
    <h3>Subscribe Newsletter</h3>
    <p>If you would like to be added to the list of parents that receive the School Newsletter,</p>
    <div class="nl-field">Email Address</div>
    <div class="nl-go">GO</div>
  </div>

  <h3 class="side abs" style="left:601px;top:603px">School Calender</h3>
  <div class="arrows abs" style="left:789px;top:606px"><span>‹</span><span>›</span></div>
  <div class="side-rule abs" style="left:601px;top:631px;width:224px"></div>
  <div class="cal abs" style="left:603px;top:638px;width:222px">
    Begins: Tuesday 14th January<br>1st Fixture Free: Friday 31st January – Monday 3rd February<br>Half-Term: Thursday 20th February – Tuesday 25th February<br>Term Ends: Thursday &nbsp;10th April
  </div>

  <h3 class="side abs" style="left:603px;top:754px">Upcoming Events</h3>
  <div class="arrows abs" style="left:791px;top:759px"><span>‹</span><span>›</span></div>
  <div class="side-rule abs" style="left:603px;top:782px;width:222px"></div>
  <div class="event abs" style="left:606px;top:788px;width:214px">
    <span class="date">Mon 04 Aug</span><b>When an unknown printer</b> took a galley of type and scra mbled it specimen book.
  </div>
  <div class="side-rule abs" style="left:605px;top:836px;width:215px"></div>
  <div class="event abs" style="left:604px;top:841px;width:214px">
    <span class="date">Mon 04 Aug</span>When an unknown printer took a galley of type and scra mbled it specimen book.
  </div>

  <h3 class="side abs" style="left:605px;top:902px">Sports Announcements</h3>
  <div class="side-rule abs" style="left:605px;top:930px;width:222px"></div>
  <ul class="sports abs" style="left:608px;top:937px">
    <li><svg width="9" height="9" viewBox="0 0 10 10"><circle cx="5" cy="5" r="4.3" fill="none" stroke="#888"/><path d="M4 3l2.5 2L4 7z" fill="#888"/></svg>Rugby</li>
    <li><svg width="9" height="9" viewBox="0 0 10 10"><circle cx="5" cy="5" r="4.3" fill="none" stroke="#888"/><path d="M4 3l2.5 2L4 7z" fill="#888"/></svg>Hockey Boys</li>
    <li><svg width="9" height="9" viewBox="0 0 10 10"><circle cx="5" cy="5" r="4.3" fill="none" stroke="#888"/><path d="M4 3l2.5 2L4 7z" fill="#888"/></svg>Soccer</li>
    <li><svg width="9" height="9" viewBox="0 0 10 10"><circle cx="5" cy="5" r="4.3" fill="none" stroke="#888"/><path d="M4 3l2.5 2L4 7z" fill="#888"/></svg>Hockey Girls</li>
    <li><svg width="9" height="9" viewBox="0 0 10 10"><circle cx="5" cy="5" r="4.3" fill="none" stroke="#888"/><path d="M4 3l2.5 2L4 7z" fill="#888"/></svg>Basketball Girls</li>
  </ul>
</aside>

<footer class="footer abs">
  <svg class="abs" style="left:74px;top:20px" width="32" height="42" viewBox="0 0 32 42"><path d="M16 0C7 0 0 7 0 16c0 11 16 26 16 26s16-15 16-26C32 7 25 0 16 0z" fill="#f4a623"/><circle cx="16" cy="15" r="5" fill="#2b2b2b"/></svg>
  <h4 class="abs" style="left:121px;top:21px">Ferndale Crest College</h4>
  <div class="small abs" style="left:120px;top:37px;width:116px;text-align:right">12 Marlow Road,<br>Brookvale 4021</div>
  <div class="small abs" style="left:116px;top:64px;text-decoration:underline">Click here to see the directions &gt;&gt;</div>
  <h4 class="abs" style="left:309px;top:26px">Download</h4>
  <div class="links abs" style="left:309px;top:44px">Registration Form<br>2nd Term 2014 Termly Calendar</div>
  <h4 class="abs" style="left:530px;top:23px">Connect With Us</h4>
  <div class="social abs"><i></i>Linkwave</div>
</footer>
<div class="copyright abs">Copyright © 2014 Ferndale Crest. All Rights Reserved.</div>
</body>
</html>
```